Software allocation system needs a business card design

We need a business card designed for our software platform - www.tallivo.com.au

At the moment the logo and website is all black and white, we are happy for suggestions on implementing some colour throughout either the logo or business card.

Industry/Entity Type

Software

Font styles to use
Sans Serif

Colors

Designer to choose colors to be used in the design.

```html
<!DOCTYPE html>
<html lang="en">
<head>
<meta charset="utf-8">
<title>Tallivo Business Card</title>
<link href="https://fonts.googleapis.com/css2?family=Montserrat:wght@300;400;600&display=swap" rel="stylesheet">
<style>
  :root {
    --bg: #d6d6d6;
    --paper: #ffffff;
    --ink: #1c1c1c;
    --band: #2a2a2a;
    --accent: #2aa7d8;
    --muted: #4a4a4a;
    --icon-disc: #8c8c8c;
  }
  * { box-sizing: border-box; margin: 0; padding: 0; }
  html, body { width: 1200px; height: 907px; overflow: hidden; }
  body {
    background: var(--bg);
    font-family: "Montserrat", Arial, sans-serif;
    color: var(--ink);
    position: relative;
  }
  .card {
    position: absolute;
    left: 320px;
    width: 560px;
    height: 320px;
    background: var(--paper);
    box-shadow: 0 6px 18px rgba(0,0,0,0.18);
    overflow: hidden;
  }
  .card--front { top: 70px; }
  .card--back { top: 470px; }

  .front-frame {
    position: absolute;
    inset: 26px;
    border: 6px solid var(--ink);
    display: flex;
    align-items: center;
    justify-content: center;
  }
  .brand {
    display: flex;
    align-items: center;
    gap: 10px;
    font-weight: 300;
    letter-spacing: 6px;
    color: var(--ink);
  }
  .brand-dot {
    border-radius: 50%;
    border: 2px solid var(--ink);
    flex: none;
  }
  .card--front .brand { font-size: 40px; }
  .card--front .brand-dot { width: 22px; height: 22px; }

  .card--back .brand {
    position: absolute;
    top: 36px; left: 40px;
    font-size: 30px;
    letter-spacing: 5px;
  }
  .card--back .brand-dot { width: 16px; height: 16px; }

  .name-block {
    position: absolute;
    top: 104px; left: 40px;
    background: var(--band);
    border: 2px solid var(--accent);
    padding: 8px 14px;
    color: #fff;
  }
  .name-block .person { font-size: 17px; font-weight: 600; letter-spacing: 0.5px; }
  .name-block .role { font-size: 14px; font-weight: 300; }

  .contact-col {
    position: absolute;
    top: 176px;
    font-size: 12.5px;
    line-height: 18px;
    color: var(--muted);
    font-weight: 400;
    white-space: nowrap;
  }
  .contact-col--phone { left: 40px; }
  .contact-col--web { left: 210px; }
  .contact-col--address { left: 390px; }

  .bottom-band {
    position: absolute;
    left: 0; right: 0; bottom: 0;
    height: 70px;
    background: var(--band);
  }
  .icon-disc {
    position: absolute;
    bottom: 48px;
    width: 34px; height: 34px;
    border-radius: 50%;
    background: var(--icon-disc);
    border: 2px solid var(--paper);
    display: flex; align-items: center; justify-content: center;
  }
  .icon-disc--phone { left: 60px; }
  .icon-disc--web { left: 230px; }
  .icon-disc--pin { left: 410px; }
</style>
</head>
<body>
  <section class="card card--front">
    <div class="front-frame">
      <div class="brand"><span class="brand-dot"></span>TALLIVO</div>
    </div>
  </section>

  <section class="card card--back">
    <div class="brand"><span class="brand-dot"></span>TALLIVO</div>

    <div class="name-block">
      <div class="person">MARCUS HALE</div>
      <div class="role">Managing Director</div>
    </div>

    <div class="contact-col contact-col--phone">
      <p>021 487 3950</p>
      <p>021 487 3951</p>
    </div>
    <div class="contact-col contact-col--web">
      <p>m.hale@tallivo.com</p>
      <p>www.tallivo.com.au</p>
    </div>
    <div class="contact-col contact-col--address">
      <p>42 Kestrel Way,</p>
      <p>Northgate Road UK</p>
    </div>

    <div class="bottom-band"></div>

    <div class="icon-disc icon-disc--phone">
      <svg width="16" height="16" viewBox="0 0 24 24" aria-hidden="true">
        <path fill="#fff" d="M6.6 10.8a15 15 0 0 0 6.6 6.6l2.2-2.2a1 1 0 0 1 1-.25 11.4 11.4 0 0 0 3.6.57 1 1 0 0 1 1 1V20a1 1 0 0 1-1 1A17 17 0 0 1 3 4a1 1 0 0 1 1-1h3.5a1 1 0 0 1 1 1c0 1.25.2 2.45.57 3.6a1 1 0 0 1-.25 1z"/>
      </svg>
    </div>
    <div class="icon-disc icon-disc--web">
      <svg width="16" height="16" viewBox="0 0 24 24" aria-hidden="true" fill="none" stroke="#fff" stroke-width="2">
        <circle cx="12" cy="12" r="9"/>
        <path d="M3 12h18M12 3c3 3.5 3 14.5 0 18M12 3c-3 3.5-3 14.5 0 18"/>
      </svg>
    </div>
    <div class="icon-disc icon-disc--pin">
      <svg width="16" height="16" viewBox="0 0 24 24" aria-hidden="true">
        <path fill="#fff" d="M12 2a7 7 0 0 0-7 7c0 5 7 13 7 13s7-8 7-13a7 7 0 0 0-7-7zm0 9.5A2.5 2.5 0 1 1 12 6.5a2.5 2.5 0 0 1 0 5z"/>
      </svg>
    </div>
  </section>
</body>
</html>
```